Business card design for a teacher - double sided, sleek design.

My name is Lina and I am an online Arabic language teacher. I am looking for a beautiful business card design for my online teaching business.

The cards will be printed in 85mm x 55mm size.
The card can be either portrait or landscape.

The design should contain my logo on one side and information on the other.

The design needs to be clean and modern. Use of subtle Arabic geometric patterns would be nice. Icons for the social media information on the card should also match the design theme.

My logo font is Consolas, which is a Monospace font.

Business card design should be delivered with editable PSD or EPS files in the handover.

Thanks

Lina

----

Information on the back:

URL: www.speakwithnadia.net [this should stand out more than other details]
Email: info@speakwithnadia.net
Instagram: @speakwithnadia
Facebook: facebook.com/speakwithnadia
Skype: speakwithnadia

My brand colours are shown in the logo attached. These are:
- Teal green - 4DC9C1
- Mango yellow - FFD600

Target Market(s)

- Young professionals
- Expatriates
- Women and Men

Industry/Entity Type

Education

Contact Information for Business Card

Information on the back:

Skype: speakwithnadia

- Teal green - 4DC9C1
- Mango yellow - FFD600

Font styles to use
Other font styles liked:
• Any font complimentary to my logo font which is a Monospace font called Consolas.

Colors

Designer to choose colors to be used in the design.

Requirements
Must have
• - Aesthetically pleasing look
• - Complimentary design with existing logo
Nice to have
• Arabic geometrical patterns

```html
<!DOCTYPE html>
<html lang="en">
<head>
<meta charset="utf-8">
<title>Speak with Nadia – Business Card</title>
<link rel="stylesheet" href="https://fonts.googleapis.com/css2?family=Montserrat:wght@400;500;700&display=swap">
<style>
  :root {
    --backdrop: #1c1c1e;
    --card: #141414;
    --card-edge: #222224;
    --teal: #4dc9c1;
    --mango: #ffd600;
    --silver: #c9c9cb;
    --ink: #f2f2f2;
    --rule: #d9d9d9;
  }
  * { margin: 0; padding: 0; box-sizing: border-box; }
  html, body {
    width: 1200px; height: 900px; overflow: hidden;
    background: var(--backdrop);
    font-family: "Montserrat", sans-serif;
  }
  .stage {
    width: 1200px; height: 900px;
    display: flex; flex-direction: column;
    align-items: center; justify-content: center; gap: 56px;
  }
  .card {
    width: 560px; height: 362px;
    background: var(--card);
    border: 1px solid var(--card-edge);
    position: relative;
  }

  /* Front */
  .card-front {
    display: flex; align-items: center; justify-content: center; gap: 22px;
  }
  .brand-square {
    width: 96px; height: 96px;
    border: 3px solid #3a3a3c;
  }
  .brand-name {
    color: var(--silver);
    font-weight: 500;
    font-size: 34px;
    letter-spacing: 4px;
    line-height: 1.15;
    text-transform: uppercase;
  }

  /* Back */
  .card-back {
    display: flex; align-items: center;
    padding: 0 30px 0 58px;
  }
  .back-brand {
    display: flex; align-items: center; gap: 12px;
    width: 170px;
  }
  .back-brand .brand-square {
    width: 74px; height: 74px; flex: none;
    border: 3px solid var(--mango);
  }
  .back-brand .brand-name {
    color: var(--teal);
    font-size: 14px; letter-spacing: 2px;
    font-weight: 700;
  }
  .divider {
    width: 2px; height: 150px;
    background: var(--rule);
    margin: 0 36px 0 22px;
  }
  .details h1 {
    color: var(--teal);
    font-weight: 700; font-size: 34px;
    letter-spacing: 2px;
    margin-bottom: 14px;
  }
  .contact-list { list-style: none; }
  .contact-list li {
    display: flex; align-items: center; gap: 10px;
    color: var(--ink);
    font-size: 16px; line-height: 23px;
  }
  .contact-list .web { font-weight: 500; font-size: 17px; }
  .contact-list svg { width: 11px; height: 11px; flex: none; }
  .dot { width: 9px; height: 9px; border-radius: 50%; background: var(--teal); flex: none; margin: 0 1px; }
</style>
</head>
<body>
<main class="stage">
  <section class="card card-front" aria-label="Card front">
    <div class="brand-square"></div>
    <div class="brand-name">Speak<br>with Nadia</div>
  </section>

  <section class="card card-back" aria-label="Card back">
    <div class="back-brand">
      <div class="brand-square"></div>
      <div class="brand-name">Speak<br>with<br>Nadia</div>
    </div>
    <div class="divider"></div>
    <div class="details">
      <h1>LINA</h1>
      <ul class="contact-list">
        <li><span class="dot"></span>@speakwithnadia</li>
        <li><span class="dot"></span>facebook.com/speakwithnadia</li>
        <li><span class="dot"></span>speakwithnadia</li>
        <li>
          <svg viewBox="0 0 12 12" aria-hidden="true"><rect x="0.8" y="2" width="10.4" height="8" fill="none" stroke="#4dc9c1" stroke-width="1.3"/><path d="M1 2.5 6 6.5 11 2.5" fill="none" stroke="#4dc9c1" stroke-width="1.3"/></svg>
          info@speakwithnadia.net
        </li>
        <li class="web">
          <svg viewBox="0 0 12 12" aria-hidden="true"><circle cx="6" cy="6" r="5.2" fill="none" stroke="#4dc9c1" stroke-width="1.2"/><ellipse cx="6" cy="6" rx="2.3" ry="5.2" fill="none" stroke="#4dc9c1" stroke-width="1"/><path d="M0.8 6h10.4" stroke="#4dc9c1" stroke-width="1"/></svg>
          www.speakwithnadia.net
        </li>
      </ul>
    </div>
  </section>
</main>
</body>
</html>
```